Christmas Banner for frontpage of website

New online scarf store just opened needs a Christmas Banner stating Free Delivery (UK only). Also if it could incorporate guaranteed Christmas delivery if ordered before 18th (might be too wordy though?) I would really like it to bring some colour to the page. The page is currently black and white with a pink accent and is very simple which is why I would like something modern and elegant, simple but with some colour. It is a shopify store I understand the banner size should be 950px by 290px the website is www.tolvarenshop.co.uk

Target Market(s)

Ladies

Industry/Entity Type

Store

Requirements
Should not have
• Not to look tacky.

```html
<!DOCTYPE html>
<html lang="en">
<head>
<meta charset="utf-8">
<title>Tolvaren – Scarf Store</title>
<link rel="stylesheet" href="https://fonts.googleapis.com/css2?family=PT+Serif&family=Open+Sans:ital,wght@1,400;1,700;1,800&display=swap">
<style>
  :root {
    --ink: #3b2a2a;
    --text: #222222;
    --muted: #888888;
    --rule: #e4e4e4;
    --nav-rule: #eee6dc;
    --accent: #c8217a;
    --topbar: #3b3a5c;
    --orange: #e85c0a;
    --headline: #5a4e52;
    --white: #ffffff;
  }
  * { box-sizing: border-box; margin: 0; padding: 0; }
  html, body { width: 1200px; height: 823px; overflow: hidden; background: var(--white); }
  body { position: relative; font-family: Arial, Helvetica, sans-serif; color: var(--text); }
  .topbar { position: absolute; top: 0; left: 0; width: 1200px; height: 4px; background: var(--topbar); }
  .utility { position: absolute; top: 15px; left: 31px; width: 1139px; height: 29px; border-bottom: 1px solid var(--rule); font-size: 11.5px; }
  .utility span, .utility a { position: absolute; top: 1px; color: var(--text); text-decoration: none; }
  .search { left: 9px; color: var(--muted) !important; }
  .search svg { vertical-align: -1px; margin-right: 6px; }
  .login { left: 294px; }
  .signup { left: 349px; }
  .cart { left: 965px; }
  .cart svg { vertical-align: -2px; margin-right: 5px; }
  .cart b { font-weight: normal; color: var(--accent); }
  .divider { left: 1059px; top: 0 !important; width: 1px; height: 16px; background: var(--rule); }
  .checkout { left: 1080px; }
  .brand { position: absolute; left: 40px; top: 78px; font-family: "PT Serif", Georgia, serif; font-size: 30px; color: var(--ink); }
  .tagline { position: absolute; right: 39px; top: 89px; font-family: "PT Serif", Georgia, serif; font-size: 14px; color: var(--ink); }
  .side-nav { position: absolute; left: 40px; top: 152px; width: 196px; list-style: none; border-top: 1px solid var(--nav-rule); }
  .side-nav li { height: 34.8px; line-height: 34px; border-bottom: 1px solid var(--nav-rule); font-size: 11.5px; font-weight: bold; color: var(--ink); }
  .social { position: absolute; left: 40px; top: 378px; display: flex; gap: 6.5px; }
  .social span { width: 22px; height: 22px; border-radius: 50%; background: var(--ink); }
  .content-rule { position: absolute; left: 325px; top: 152px; width: 836px; border-top: 1px solid var(--rule); }
  .banner { position: absolute; left: 315px; top: 171px; width: 846px; height: 258px; overflow: hidden; border: 1px solid #dcdcdc;
    background: linear-gradient(155deg, #8fd9f0 0%, #f7f4fb 22%, #f8c6e0 45%, #f9efb0 62%, #d8f0b8 75%, #bfe8f4 90%, #ffffff 100%); }
  .banner-wash { position: absolute; inset: 0; background: linear-gradient(90deg, rgba(255,255,255,0) 0%, rgba(255,255,255,.55) 35%, rgba(255,255,255,.85) 70%, #ffffff 100%); }
  .banner-photo { position: absolute; right: 0; top: 0; width: 245px; height: 258px;
    background: linear-gradient(180deg, #f2ede6 0%, #e8c596 40%, #ec8a7c 75%, #c9a674 100%); }
  .banner h1 { position: absolute; left: 64px; top: 34px; font-family: "Open Sans", Arial, sans-serif; font-style: italic; font-weight: 800; font-size: 55px; letter-spacing: -1px; color: var(--headline); }
  .banner .promise { position: absolute; left: 64px; top: 101px; font-family: "Open Sans", Arial, sans-serif; font-style: italic; font-weight: 800; font-size: 27px; color: var(--orange); }
  .banner .condition { position: absolute; right: 386px; top: 141px; font-family: "Open Sans", Arial, sans-serif; font-style: italic; font-size: 18px; color: var(--headline); }
  .banner .cta { position: absolute; left: 303px; top: 195px; width: 169px; height: 39px; border-radius: 20px; background: var(--orange); color: var(--white);
    font-family: "Open Sans", Arial, sans-serif; font-style: italic; font-weight: 700; font-size: 19px; line-height: 39px; text-align: center; }
  .product { position: absolute; top: 476px; width: 267px; text-align: center; }
  .product .photo { width: 267px; height: 267px; }
  .product .name { margin-top: 15px; font-size: 11px; color: var(--text); }
  .product .name.featured { color: var(--accent); }
  .product .price { margin-top: 5px; font-family: "PT Serif", Georgia, serif; font-size: 14.5px; color: var(--ink); }
  .p1 { left: 342px; } .p2 { left: 628px; } .p3 { left: 912px; }
  .p1 .photo { background: radial-gradient(ellipse at center, #ffffff 22%, #2f8a6e 38%, #b8306a 60%, #ffffff 72%); }
  .p2 .photo { background: linear-gradient(135deg, #e4e4e4, #cfd1d1 60%, #d9d9d9); }
  .p3 .photo { background: radial-gradient(ellipse at center, #d9265a 0%, #c01f55 45%, #ffffff 72%); }
</style>
</head>
<body>
  <div class="topbar"></div>
  <nav class="utility">
    <span class="search"><svg width="10" height="10" viewBox="0 0 10 10"><circle cx="4" cy="4" r="3" fill="none" stroke="#222" stroke-width="1.6"/><line x1="6.2" y1="6.2" x2="9.3" y2="9.3" stroke="#222" stroke-width="1.8"/></svg>Search</span>
    <a class="login" href="#">Login</a>
    <a class="signup" href="#">Sign Up</a>
    <a class="cart" href="#"><svg width="17" height="13" viewBox="0 0 17 13"><path d="M0 1h3l2 8h9l2-6H4.5" fill="none" stroke="#222" stroke-width="1.5"/><circle cx="6" cy="11.5" r="1.3" fill="#222"/><circle cx="13" cy="11.5" r="1.3" fill="#222"/></svg>My Cart <b>(0)</b></a>
    <span class="divider"></span>
    <a class="checkout" href="#">Check Out</a>
  </nav>

  <div class="brand">Tolvaren</div>
  <div class="tagline">FREE DELIVERY - Love Your Neck</div>

  <ul class="side-nav">
    <li>Home</li>
    <li>Funky Scarves</li>
    <li>Thicker Scarves</li>
    <li>Thin Scarves</li>
    <li>Blog</li>
    <li>About Us</li>
  </ul>
  <div class="social"><span></span><span></span><span></span><span></span><span></span></div>

  <div class="content-rule"></div>

  <section class="banner">
    <div class="banner-wash"></div>
    <div class="banner-photo" role="img" aria-label="Smiling blonde woman wearing a coral knitted snood"></div>
    <h1>Free Delivery</h1>
    <p class="promise">Guaranteed Christmas delivery</p>
    <p class="condition">if ordered before 18th</p>
    <div class="cta">Order Now</div>
  </section>

  <article class="product p1">
    <div class="photo" role="img" aria-label="Chunky knitted snood in green, pink and yellow"></div>
    <p class="name featured">Elsie Snood</p>
    <p class="price">£10.50</p>
  </article>
  <article class="product p2">
    <div class="photo" role="img" aria-label="Light grey scarf printed with swallows"></div>
    <p class="name">Mira Scarf</p>
    <p class="price">£9.75</p>
  </article>
  <article class="product p3">
    <div class="photo" role="img" aria-label="Pink and red striped scarf with fringed ends"></div>
    <p class="name">Nell scarf</p>
    <p class="price">£9.75</p>
  </article>
</body>
</html>
```